Wedding filmmaker needs artistic business card design - brightwaterreels.ca

We are high end wedding filmmakers in a major market who produce cinematic wedding films. We require a business card design that communicates our quality, artistry, and professionalism yet looks progressive and friendly. Colors and design should skew appeal more to the bride-to-be who is usually the decision maker but not be overtly feminine per se. This means generally light pastel shades of ivory, purple, pink, yellow, as examples.
We already have a name logo established: the words "Brightwater Reels" in the font Great Vibes. Designs must use Kraft natural cardstock as the print stock and am leaning heavily toward our name logo in white, but I am open to black as well. Please design any color elements with spot white underneath where possible.
Do not try to compliment or take inspiration from our website design. Treat the card design as a separate stand alone.
Thank you so much for your hard work!

Target Market(s)

Affluent couples spending $50,000+ on their wedding

Industry/Entity Type

Progressive

Contact Information for Business Card

Peter Brightwater
Producer
905-482-7139
www.brightwaterreels.ca
peter@brightwaterreels.ca
twitter @brightwater287

Font styles to use
Serif
Sans Serif

Requirements
Must have
• - Brightwater Reels name logo (reference GIF uploaded for reference only) and catch phrase: Breathtaking wedding films (I'm open to capitalizing all three words, or just first, or all in small caps). I favor logo, and catch phrase on front of card and my contact details on the other side but if you feel strongly about a different design, go for it!
• - Design must be submitted shown on Kraft natural cardstock NOT WHITE cardstock, If you're not familiar with Kraft, this is what it looks like: http://www.quillandlatchjournal.com/wp-content/uploads/2013/07/il_570xN.382745196_kq3m.jpg
Nice to have
• - An original graphic element (eg. movie reel, bouquet, confetti, etc.) that compliments the name logo but is subtle and discreet, doesn't overpower or entangle it.
• -Great use of balance, composition, negative space, etc. I like clean tasteful design
Should not have
• -Lousy boring clip art.
• -Graphic elements, fonts, or color palette from our website
• -White cardstock background
• -designs you have previously submitted for other contests
• -Bold dark colors (eg. red, orange navy blue, etc.)
• -High tech futuristic designs like you'd create for a software company

```html
<!DOCTYPE html>
<html lang="en">
<head>
<meta charset="utf-8">
<title>Brightwater Reels — Business Card</title>
<link rel="stylesheet" href="https://fonts.googleapis.com/css2?family=Alegreya+Sans:wght@400;500;700&display=swap">
<style>
  :root {
    --backdrop: #cdcdcd;
    --kraft: #c5a47c;
    --kraft-light: #cbab84;
    --ink-white: #ffffff;
    --ink-black: #1c1712;
  }
  html, body {
    margin: 0;
    padding: 0;
    width: 1200px;
    height: 750px;
    overflow: hidden;
    background: var(--backdrop);
    font-family: "Alegreya Sans", sans-serif;
  }
  .stage {
    position: relative;
    width: 1200px;
    height: 750px;
  }
  .card {
    position: absolute;
    top: 226px;
    width: 488px;
    height: 298px;
    background: radial-gradient(ellipse at 40% 40%, var(--kraft-light), var(--kraft));
    overflow: hidden;
  }
  .card--back { left: 100px; }
  .card--front { left: 615px; }

  /* Back: contact side */
  .person {
    position: absolute;
    top: 74px;
    left: 0;
    width: 100%;
    text-align: center;
  }
  .person__name {
    margin: 0;
    color: var(--ink-white);
    font-weight: 400;
    font-size: 25px;
    letter-spacing: 0.5px;
    line-height: 1;
  }
  .person__title {
    margin: 9px 0 0;
    color: var(--ink-black);
    font-weight: 500;
    font-size: 12.5px;
    letter-spacing: 3.2px;
    line-height: 1;
  }
  .contact {
    position: absolute;
    top: 160px;
    left: 0;
    width: 100%;
    margin: 0;
    padding: 0;
    list-style: none;
    text-align: center;
  }
  .contact__item {
    color: var(--ink-white);
    font-size: 18px;
    line-height: 28px;
    letter-spacing: 0.3px;
  }
  .contact__label {
    color: var(--ink-black);
    font-weight: 700;
    font-size: 13px;
    margin-right: 5px;
  }

  /* Front: brand side */
  .brand {
    position: absolute;
    top: 60px;
    left: 0;
    width: 100%;
    text-align: center;
  }
  .brand__name {
    margin: 0;
    color: var(--ink-white);
    font-weight: 400;
    font-size: 44px;
    line-height: 1;
    letter-spacing: 0.5px;
  }
  .brand__tagline {
    margin: 8px 0 0;
    color: var(--ink-black);
    font-weight: 500;
    font-size: 12px;
    letter-spacing: 2px;
    line-height: 1;
  }
  .bouquet {
    position: absolute;
    right: 0;
    bottom: 0;
    width: 370px;
    height: 146px;
  }
  .bouquet__fill { fill: var(--ink-white); }
</style>
</head>
<body>
  <main class="stage">
    <section class="card card--back" aria-label="Card back with contact details">
      <div class="person">
        <h2 class="person__name">Peter Brightwater</h2>
        <p class="person__title">PRODUCER</p>
      </div>
      <ul class="contact">
        <li class="contact__item"><span class="contact__label">M</span>905-482-7139</li>
        <li class="contact__item"><span class="contact__label">E</span>peter@brightwaterreels.ca</li>
        <li class="contact__item"><span class="contact__label">W</span>www.brightwaterreels.ca</li>
        <li class="contact__item"><span class="contact__label">T</span>@brightwater287</li>
      </ul>
    </section>

    <section class="card card--front" aria-label="Card front with brand name">
      <div class="brand">
        <h1 class="brand__name">Brightwater Reels</h1>
        <p class="brand__tagline">BREATHTAKING WEDDING FILMS</p>
      </div>
      <svg class="bouquet" viewBox="0 0 370 146" role="img" aria-label="White illustration of a cluster of roses rising toward the lower right corner">
        <path class="bouquet__fill" d="M0 146 C30 120 70 84 120 76 C160 60 200 48 240 40 C270 20 310 6 345 0 L370 0 L370 146 Z"/>
      </svg>
    </section>
  </main>
</body>
</html>
```